Young, modern, highly skilled carpenter needs business card design

I need a business card design for my construction business. Its called 'Barlow Construction Services'. Im looking for a ultra modern design that incorporates B C S, the first letters of the name with only a subtle reference to carpentry. The design should reflect my high quality work and eye for detail. i have also uploaded some exmaple designs i like.

Industry/Entity Type

Construction

Requirements
Must have
• Name of business, my name, mobile number, ABN number, email address
Nice to have
• A logo incorporating the name of the business

```html
<!DOCTYPE html>
<html lang="en">
<head>
<meta charset="utf-8">
<title>Barlow Construction Services – Business Card</title>
<link href="https://fonts.googleapis.com/css2?family=Carlito:wght@400;700&display=swap" rel="stylesheet">
<style>
  :root {
    --backdrop: #7f8f8f;
    --brand-green: #4cff00;
    --ink: #1e1e24;
    --paper: #ffffff;
  }
  html, body {
    margin: 0;
    padding: 0;
    overflow: hidden;
  }
  .canvas {
    position: relative;
    width: 1200px;
    height: 900px;
    background: var(--backdrop);
    font-family: "Carlito", "Calibri", sans-serif;
    overflow: hidden;
  }
  .card {
    position: absolute;
    left: 335px;
    width: 541px;
    height: 372px;
  }
  .card--front {
    top: 60px;
    background: var(--brand-green);
  }
  .card--back {
    top: 459px;
    background: var(--paper);
  }
  .wordmark {
    position: absolute;
    margin: 0;
    font-weight: 700;
    line-height: 1;
    letter-spacing: 0.22em;
  }
  .card--front .wordmark {
    left: 55px;
    top: 262px;
    font-size: 66px;
    color: var(--paper);
  }
  .card--back .wordmark {
    left: 330px;
    top: 252px;
    font-size: 46px;
    color: var(--ink);
  }
  .contact {
    position: absolute;
    left: 67px;
    top: 52px;
    margin: 0;
    font-size: 19px;
    line-height: 26px;
    color: var(--brand-green);
  }
  .contact__name {
    display: block;
    font-weight: 700;
    font-size: 21px;
    color: var(--ink);
  }
  .contact__divider {
    color: var(--ink);
  }
  .company-name {
    position: absolute;
    left: 65px;
    top: 296px;
    margin: 0;
    font-size: 23px;
    font-weight: 700;
    color: var(--brand-green);
    white-space: nowrap;
  }
</style>
</head>
<body>
<main class="canvas">
  <section class="card card--front">
    <p class="wordmark">BCS</p>
  </section>

  <section class="card card--back">
    <p class="contact">
      <span class="contact__name">Liam Barlow</span>
      liam_barlow@mailbox.com<br>
      0412 583206 <span class="contact__divider">//</span> ABN 51 824 307 619
    </p>
    <p class="wordmark">BCS</p>
    <p class="company-name">BARLOW CONSTRUCTION SERVICES</p>
  </section>
</main>
</body>
</html>
```